Hearthwell Climate Business Card Design

Design new, 2 sides, business cards for a residential and light commercial heating, air conditioning contractor.

Target Market(s)

Homeowners, small businesses

Industry/Entity Type

Business

Contact Information for Business Card

Dominic Westerhall
Phone - 862-415-2736
Email
Address - PO box 518
Brightwater NJ 07912
Website - www.HarborBreezeLLC.example

Requirements
Must have
• logo, company colors, standard size with no die cut, so I can use nova stamp

```html
<!DOCTYPE html>
<html lang="en">
<head>
<meta charset="utf-8">
<title>Hearthwell Climate Business Card</title>
<link rel="stylesheet" href="https://fonts.googleapis.com/css2?family=Source+Sans+3:ital,wght@0,400;0,600;0,700;1,400&display=swap">
<style>
  :root {
    --crimson: #9b1f32;
    --orange: #f39131;
    --gold: #f3a640;
    --white: #ffffff;
    --ink: #2b2b2b;
    --stage: #e4e4e4;
  }
  * { box-sizing: border-box; margin: 0; padding: 0; }
  html, body {
    width: 1105px; height: 1200px; overflow: hidden;
    background: var(--stage);
    font-family: "Source Sans 3", "Helvetica Neue", Arial, sans-serif;
  }
  .canvas { position: relative; width: 1105px; height: 1200px; }
  .card {
    position: absolute; left: 196px; width: 720px; height: 412px;
    border-radius: 25px; overflow: hidden;
  }
  .card--front {
    top: 145px;
    background:
      radial-gradient(ellipse 60% 70% at 50% 50%, var(--crimson) 60%, transparent 100%),
      linear-gradient(135deg, var(--orange) 0%, var(--crimson) 28%, var(--crimson) 68%, var(--orange) 100%);
  }
  .card--back { top: 602px; background: var(--white); }

  .info-panel {
    position: absolute; left: 100px; right: 100px; top: 22px; bottom: 22px;
    border: 7px solid var(--white); border-radius: 30px;
    background: var(--crimson);
    display: flex; flex-direction: column; align-items: center;
    padding-top: 62px; color: var(--white); text-align: center;
  }
  .contact-name { color: var(--gold); font-size: 26px; font-weight: 600; letter-spacing: 0.5px; line-height: 1.1; }
  .contact-title { font-size: 20px; line-height: 1.2; }
  .contact-address { font-size: 19px; line-height: 1.35; margin-top: 14px; }
  .contact-phones { display: flex; gap: 12px; font-size: 19px; margin-top: 16px; }
  .contact-line { display: flex; align-items: center; gap: 6px; font-size: 19px; line-height: 1.45; }
  .contact-phones .contact-line { line-height: 1.2; }
  .icon { width: 16px; height: 16px; fill: var(--gold); flex: none; }

  .brand-name {
    position: absolute; left: 0; right: 0; top: 160px;
    text-align: center; color: var(--crimson);
    font-size: 54px; font-weight: 700; letter-spacing: 1px; line-height: 1;
  }
  .tagline {
    position: absolute; left: 0; right: 0; top: 327px;
    text-align: center; color: var(--ink);
    font-size: 19px; font-style: italic; line-height: 1.3;
  }
</style>
</head>
<body>
<main class="canvas">
  <section class="card card--front" aria-label="Business card front">
    <div class="info-panel">
      <p class="contact-name">DOMINIC WESTERHALL</p>
      <p class="contact-title">CEO/Founder</p>
      <p class="contact-address">PO box 518<br>Brightwater NJ 07912</p>
      <div class="contact-phones">
        <span class="contact-line">
          <svg class="icon" viewBox="0 0 16 16"><path d="M3 1l3 3-1.6 2a9 9 0 0 0 5.6 5.6L12 10l3 3-2 2C6 15 1 10 1 3z"/></svg>862 415 2736
        </span>
        <span class="contact-line">
          <svg class="icon" viewBox="0 0 16 16"><path d="M4 0h8a1 1 0 0 1 1 1v14a1 1 0 0 1-1 1H4a1 1 0 0 1-1-1V1a1 1 0 0 1 1-1zm1 2v10h6V2zm3 11a1 1 0 1 0 0 2 1 1 0 0 0 0-2z"/></svg>862 415 2790
        </span>
        <span class="contact-line">
          <svg class="icon" viewBox="0 0 16 16"><path d="M4 1h8v4H4zM1 6h14v7h-3v2H4v-2H1zm4 5v3h6v-3z"/></svg>862 415 2741
        </span>
      </div>
      <span class="contact-line">
        <svg class="icon" viewBox="0 0 16 16"><path d="M1 3h14v10H1zm1 1v.5l6 4 6-4V4z"/></svg>dominic@hearthwellclimate.example
      </span>
      <span class="contact-line">
        <svg class="icon" viewBox="0 0 16 16"><circle cx="8" cy="8" r="7"/></svg>www.HearthwellClimateLLC.example
      </span>
    </div>
  </section>

  <section class="card card--back" aria-label="Business card back">
    <p class="brand-name">Hearthwell Climate</p>
    <p class="tagline">Residential &amp; light commercial heating<br>Air conditioning contractor</p>
  </section>
</main>
</body>
</html>
```